Varnex Consulting Business card design.

See our website www.varnexconsulting.example which will give you a good idea of what we are about. The font is called 'Play'.

I'd like a standout business card in keeping with the themes and branding on the website

Target Market(s)

professionals. HR directors

Industry/Entity Type

Business

Contact Information for Business Card

Varnex Consulting PO Box 3172 Merrowdale NSW 2291 1300 485 193 Gavin Threlkeld Principal email: career@varnexconsulting.example ABN: 71203948865

Font styles to use
Other font styles liked:
• Play

Requirements
Must have
• Must have same design colours and branding as website.
• On back I'd prefer a list of the things we do which appears below the name at the header on the website

```html
<!DOCTYPE html>
<html lang="en">
<head>
<meta charset="utf-8">
<title>Varnex Consulting – Business Card</title>
<link rel="stylesheet" href="https://fonts.googleapis.com/css2?family=Play:wght@400;700&display=swap">
<style>
  :root {
    --page-bg: #a3a3a1;
    --navy: #0d2136;
    --brand-blue: #3a90d2;
    --tag-blue: #2f78b8;
    --ink: #111418;
    --white: #ffffff;
    --photo-dark: #5a4746;
    --photo-light: #a27866;
  }
  * { box-sizing: border-box; margin: 0; padding: 0; }
  html, body {
    width: 992px;
    height: 1200px;
    overflow: hidden;
    background: var(--page-bg);
    font-family: "Play", sans-serif;
  }
  .card {
    position: absolute;
    left: 99px;
    width: 806px;
    height: 462px;
    border-radius: 22px;
    overflow: hidden;
    background: var(--white);
    box-shadow: 0 6px 14px rgba(0,0,0,0.35);
  }
  .card--front { top: 103px; }
  .card--back { top: 625px; }

  .header {
    position: absolute;
    left: 0; top: 0;
    width: 100%;
    background: var(--navy);
  }
  .card--front .header { height: 188px; }
  .card--back .header { height: 168px; }

  .wordmark {
    position: absolute;
    color: var(--brand-blue);
    font-size: 54px;
    font-weight: 400;
    letter-spacing: 2px;
    line-height: 1;
    white-space: nowrap;
  }
  .services {
    position: absolute;
    color: var(--tag-blue);
    font-size: 17px;
    letter-spacing: 2.4px;
    white-space: nowrap;
  }
  .services .sep { margin: 0 5px; }

  .card--front .wordmark { left: 37px; top: 48px; }
  .card--front .services { left: 36px; top: 127px; }
  .card--back .wordmark { left: 0; width: 100%; text-align: center; top: 36px; }
  .card--back .services { left: 0; width: 100%; text-align: center; top: 113px; }

  .person {
    position: absolute;
    right: 33px;
    top: 210px;
    text-align: right;
  }
  .person__name { color: var(--brand-blue); font-size: 28px; line-height: 1.2; }
  .person__role { color: var(--ink); font-size: 25px; line-height: 1.3; }

  .abn {
    position: absolute;
    left: 29px; top: 303px;
    color: var(--ink);
    font-size: 21px;
  }
  .contacts {
    position: absolute;
    left: 30px; top: 343px;
    list-style: none;
  }
  .contacts li {
    display: flex;
    align-items: center;
    height: 33px;
    color: var(--ink);
    font-size: 20px;
  }
  .contacts svg { width: 16px; height: 16px; margin-right: 13px; flex: none; }

  .photo {
    position: absolute;
    left: 0; top: 168px;
    width: 100%;
    height: 294px;
    background: linear-gradient(180deg, var(--photo-dark) 0%, var(--photo-light) 100%);
  }
</style>
</head>
<body>

<section class="card card--front" aria-label="Business card front">
  <header class="header">
    <h1 class="wordmark">VARNEX CONSULTING</h1>
    <p class="services">Search &amp; Select<span class="sep">|</span>Career<span class="sep">|</span>Coaching<span class="sep">|</span>Leadership<span class="sep">|</span>Outplacement</p>
  </header>

  <div class="person">
    <p class="person__name">Gavin Threlkeld</p>
    <p class="person__role">Principal</p>
  </div>

  <p class="abn">ABN: 71203948865</p>

  <ul class="contacts">
    <li>
      <svg viewBox="0 0 16 16" aria-hidden="true"><rect width="16" height="16" rx="2" fill="#3a90d2"/><path d="M3.5 6.5c0-1.5 2-2.5 4.5-2.5s4.5 1 4.5 2.5v.8h-2.2v-1H5.7v1H3.5z M5 8.5h6l1 4H4z" fill="#fff"/></svg>
      1300 485 193
    </li>
    <li>
      <svg viewBox="0 0 16 16" aria-hidden="true"><rect width="16" height="16" rx="2" fill="#3a90d2"/><rect x="3" y="4.5" width="10" height="7" fill="#fff"/><path d="M3 4.5l5 4 5-4" fill="none" stroke="#3a90d2" stroke-width="1"/></svg>
      career@varnexconsulting.example
    </li>
    <li>
      <svg viewBox="0 0 16 16" aria-hidden="true"><rect width="16" height="16" rx="2" fill="#3a90d2"/><path d="M8 13.5s-3.5-4-3.5-6.5a3.5 3.5 0 0 1 7 0c0 2.5-3.5 6.5-3.5 6.5z" fill="#fff"/><circle cx="8" cy="7" r="1.3" fill="#3a90d2"/></svg>
      PO Box 3172 Merrowdale NSW 2291
    </li>
  </ul>
</section>

<section class="card card--back" aria-label="Business card back">
  <header class="header">
    <h2 class="wordmark">VARNEX CONSULTING</h2>
    <p class="services">Search &amp; Select<span class="sep">|</span>Career<span class="sep">|</span>Coaching<span class="sep">|</span>Leadership<span class="sep">|</span>Outplacement</p>
  </header>
  <div class="photo" role="img" aria-label="Photograph: close-up of sprinters' hands on the starting line of a running track"></div>
</section>

</body>
</html>
```